IT Consulting Business needs a web design

We need a web design for an IT Consulting company called "Vorensk". We want to replace the existing web site (www.vorensk-example.com) with a new design. Our services are IT Consulting, IT Training, IT Outsourcing.
We would like to see designs that communicate "Trusted IT Advisor" with modern & bold design.

We would like to see the design of 2 pages:
1. Home page (www.vorensk-example.com)
2. The detail page (http://www.vorensk-example.com/index_files/consulting.htm)

Industry/Entity Type

Business

```html
<!DOCTYPE html>
<html lang="en">
<head>
<meta charset="utf-8">
<title>Vorensk – IT Consulting</title>
<link rel="stylesheet" href="https://fonts.googleapis.com/css2?family=Arimo:wght@400;700&family=PT+Sans&family=Questrial&family=Raleway:wght@200;300&display=swap">
<style>
:root{
  --red:#ff3b3f;
  --red-soft:#ff7577;
  --blue:#0d4fa8;
  --ink:#3a3a3a;
  --text:#444;
  --page:#f4f4f4;
  --footer:#2b2b2b;
  --white:#fff;
}
*{box-sizing:border-box;margin:0;padding:0}
html,body{width:1200px;height:1195px;overflow:hidden}
body{position:relative;background:var(--page);font-family:"Questrial",sans-serif;color:var(--text)}
.abs{position:absolute}
.top-band{left:0;top:6px;width:1200px;height:405px;background:radial-gradient(ellipse at 50% 30%,var(--red-soft) 0%,var(--red) 70%)}
.brand-tab{left:155px;top:6px;width:201px;height:114px}
.brand-name{left:155px;top:36px;width:201px;text-align:center;font-family:"Arimo",sans-serif;font-weight:700;font-size:37px;color:var(--blue);letter-spacing:-.5px}
.contact{top:31px;font-family:"PT Sans",sans-serif;font-size:16px;color:var(--white);display:flex;align-items:center;gap:6px}
.main-nav{left:496px;top:74px;width:547px;height:47px;border-radius:8px;background:linear-gradient(#4a8fe6,#1a5fc2);display:flex;align-items:center;padding-left:12px;box-shadow:0 2px 4px rgba(0,0,0,.2)}
.main-nav a{font-family:"PT Sans",sans-serif;font-size:14.5px;color:#dfeaff;text-decoration:none;padding:0 17px;border-left:1px solid rgba(255,255,255,.35);line-height:16px}
.main-nav a:first-child{border-left:0;color:var(--white)}
.hero{left:157px;top:146px;width:886px;height:369px;background:radial-gradient(ellipse at 25% 30%,#4b6585 0%,#2b3f58 55%,#1b2a3d 100%);overflow:hidden}
.hero-photo{position:absolute;right:0;top:0;width:480px;height:369px;background:radial-gradient(ellipse 60% 70% at 62% 38%,rgba(201,165,140,.85) 0%,rgba(109,122,136,.6) 40%,rgba(30,30,36,.55) 75%,rgba(30,30,36,0) 100%)}
.hero-title{left:26px;top:24px;font-family:"Raleway",sans-serif;font-weight:200;color:var(--white);line-height:58px}
.hero-title span{display:block;font-size:56px}
.hero-title .caps{font-size:55px;font-weight:300;letter-spacing:1px}
.hero-shadow{top:515px;height:22px;background:radial-gradient(ellipse at 50% 0%,rgba(0,0,0,.35),rgba(0,0,0,0) 70%)}
.service{top:560px;width:280px}
.service h2,.section-title{font-family:"Arimo",sans-serif;font-weight:700;font-size:19px}
.service h2 .lead{color:var(--red)}
.service h2 .tail{color:var(--blue)}
.frame{background:var(--white);border:1px solid #d6d6d6;padding:6px}
.service .frame{margin-top:9px;height:140px}
.photo{width:100%;height:100%}
.service p{margin-top:13px;font-size:11.5px;line-height:14.6px;text-align:justify;height:70px}
.btn{display:inline-block;width:66px;height:28px;border-radius:3px;background:linear-gradient(#ff4d4d,#e80f12);color:var(--white);font-family:"Arimo",sans-serif;font-size:14px;line-height:28px;text-align:center;text-decoration:none;box-shadow:0 1px 2px rgba(0,0,0,.2)}
.divider{left:157px;top:858px;width:886px;height:1px;background:#d3d3d3}
.section-title{color:var(--ink);font-size:19.5px}
.trusted-copy{left:444px;top:910px;width:320px;font-size:11.9px;line-height:16.6px}
.expertise-list{left:799px;top:918px;width:245px;list-style:none;font-size:11.8px;line-height:14.8px}
.expertise-list li{position:relative;padding-left:24px;margin-bottom:5px}
.expertise-list li::before{content:"";position:absolute;left:3px;top:3px;width:3px;height:3px;background:var(--red);box-shadow:4px 0 var(--red),0 4px var(--red),4px 4px var(--red)}
.site-footer{left:0;top:1107px;width:1200px;height:88px;background:var(--footer)}
.footer-nav{left:155px;top:1126px;font-family:"Arimo",sans-serif;font-size:12.5px;color:var(--white)}
.footer-nav a{color:var(--white);text-decoration:none}
.footer-nav a.current{color:var(--red)}
.footer-nav .sep{margin:0 9px}
.copyright{left:155px;top:1147px;font-family:"Arimo",sans-serif;font-size:12.5px;color:var(--white)}
.social{left:954px;top:1126px;display:flex;gap:4px}
.social span{width:27px;height:27px;border-radius:4px;background:linear-gradient(#ff4a4a,#e00c10)}
</style>
</head>
<body>
<div class="abs top-band"></div>

<svg class="abs brand-tab" viewBox="0 0 201 114" aria-hidden="true"><polygon points="0,0 201,0 201,86 100,114 0,86" fill="#fff"/></svg>
<div class="abs brand-name">Vorensk</div>

<div class="abs contact" style="left:728px">
  <svg width="18" height="14" viewBox="0 0 18 14" aria-hidden="true"><path d="M2 5c0-3 14-3 14 0v2h-4V5H6v2H2z M5 7h8l2 6H3z" fill="#fff"/></svg>1300 555 019
</div>
<div class="abs contact" style="left:872px">
  <svg width="14" height="10" viewBox="0 0 14 10" aria-hidden="true"><rect x=".5" y=".5" width="13" height="9" fill="#fff" stroke="#ddd"/><path d="M.5 .5 7 6l6.5-5.5" fill="none" stroke="#aaa"/></svg>info@vorensk-example.com
</div>

<nav class="abs main-nav">
  <a href="#">Home</a><a href="#">About us</a><a href="#">Services</a><a href="#">Expertises</a><a href="#">Careers</a><a href="#">Contact Us</a>
</nav>

<section class="abs hero">
  <div class="hero-photo" role="img" aria-label="Smiling consultant in a dark suit pointing toward the headline"></div>
  <h1 class="abs hero-title"><span>Professional</span><span class="caps">CONSULTING</span></h1>
</section>
<div class="abs hero-shadow" style="left:185px;width:380px"></div>
<div class="abs hero-shadow" style="left:640px;width:380px"></div>

<article class="abs service" style="left:155px">
  <h2><span class="lead">Consulting</span> <span class="tail">Services</span></h2>
  <div class="frame"><div class="photo" role="img" aria-label="Team of colleagues meeting around a computer" style="background:linear-gradient(120deg,#5c6b55,#d9c8a8 45%,#c8cf9e 75%,#8c9a7d)"></div></div>
  <p>Our experienced, certified professionals provides IT consulting using industry recommended practices. We are specialized in Corvane Business Productivity Platform using Corvane TeamPortal..</p>
  <a class="btn" href="#">more</a>
</article>

<article class="abs service" style="left:460px">
  <h2><span class="lead">Training</span> <span class="tail">Services</span></h2>
  <div class="frame"><div class="photo" role="img" aria-label="Hand with a pen pointing at charts on a screen" style="background:linear-gradient(100deg,#1d2a44,#6f88b5 40%,#c5d6ef 65%,#2b3f66)"></div></div>
  <p>Our certified trainers provide in-house training for Vorensk original courses as well as customized training courses that suit your organization needs. On-Site training..</p>
  <a class="btn" href="#">more</a>
</article>

<article class="abs service" style="left:765px">
  <h2><span class="lead">Solution</span> <span class="tail">Services</span></h2>
  <div class="frame"><div class="photo" role="img" aria-label="Hands using a phone and tablet showing charts" style="background:linear-gradient(110deg,#e8e8ea,#cfcfd2 40%,#9aa3ad 65%,#d9b99a)"></div></div>
  <p>Vorensk's unique solution services offer customers with the benefits of our expert consultants in designing, deploying, and implementing our solutions. Customers who want to have the solution with..</p>
  <a class="btn" href="#">more</a>
</article>

<div class="abs divider"></div>

<h2 class="abs section-title" style="left:156px;top:877px">Most Trusted IT Consultant</h2>
<div class="abs frame" style="left:157px;top:909px;width:272px;height:168px">
  <div class="photo" role="img" aria-label="Support team with headset in a bright office" style="background:linear-gradient(90deg,#d9c9b6,#c9d3de 45%,#8d9db1 75%,#e6ebf0)"></div>
</div>
<p class="abs trusted-copy">We are experienced, certified professionals who are experts at Information Technology (IT) consulting, solution design &amp; development, and training for medium-size businesses and large enterprises. We are committed to helping our clients quickly achieve the most appropriate solution with sustainable ROI. We are focusing on Corvane Technologies for large organizations. We offer the agility of a smaller firm, the quality of larger firms.</p>
<a class="abs btn" href="#" style="left:445px;top:1049px">more</a>

<h2 class="abs section-title" style="left:800px;top:876px">Our Expertises</h2>
<ul class="abs expertise-list">
  <li>Corvane TeamPortal Technologies</li>
  <li>Business Intelligence with Velmara Query Server</li>
  <li>Enterprise Integration with Plenwick Relay Server</li>
  <li>Ostrivel Development</li>
  <li>Nimbrel Flow</li>
</ul>

<footer class="abs site-footer"></footer>
<nav class="abs footer-nav">
  <a class="current" href="#">Home</a><span class="sep">|</span><a href="#">About Us</a><span class="sep">|</span><a href="#">Services</a><span class="sep">|</span><a href="#">Careers</a><span class="sep">|</span><a href="#">Expertises</a><span class="sep">|</span><a href="#">Contact Us</a>
</nav>
<p class="abs copyright">Vorensk © 2013. All Rights Reserved.</p>
<div class="abs social" aria-label="Social links"><span></span><span></span><span></span></div>
</body>
</html>
```